Electrical Contractor Brochure, Folder and Letter Head

Brightwell Power Ltd. is an Edmonton based electrical contractor focusing on commercial and industrial electrical services. Our target market is manufacturing facilities, warehouses and commercial buildings.

We want to seem larger than we are with service vehicles and electricians ready to dispatch to service calls and new installations. Our key color is the blue in the logo. The BWP logo is well branded in Edmonton and should be on the brochure.

We are looking for a tri-fold brochure, full-page brochure with folder sleeves and a letter head.
Updates

Please ignore the second page of copy.  I only want the electrical content in the brochure.  This is my mistake.  Please use only the first page of copy.

Industry/Entity Type

Electrical

Requirements
Must have
• Many background pics of the services, electricians and projects. I like the faded BWP logo in the background of the letterhead! Folder Size A4
Nice to have
• Try the pic named Cover Pic1 to on the front of the brochure.
Should not have
• DO NOT USE ANY WEBSITE CONTENT. THIS IS NOT OUR BUSINESS. PLEASE USE ONLY CONTENT AND COLOR FROM THE ATTACHED FILES!!

```html
<!DOCTYPE html>
<html lang="en">
<head>
<meta charset="utf-8">
<title>Brightwell Power Ltd. — Letterhead and Folder</title>
<link rel="stylesheet" href="https://fonts.googleapis.com/css2?family=Ubuntu:wght@400;500;700&display=swap">
<style>
  :root {
    --stage: #eceef1;
    --brand-blue: #2f5fa8;
    --brand-navy: #263a78;
    --band-purple: #4a4a88;
    --band-sky: #56a8de;
    --band-blue: #3a78bb;
    --folder-grey: #d6d7da;
    --folder-dark: #353538;
    --ink: #2a2a2e;
    --watermark: rgba(120, 130, 145, 0.28);
  }
  * { margin: 0; padding: 0; box-sizing: border-box; }
  html, body { width: 1200px; height: 673px; overflow: hidden; }
  body {
    background: var(--stage);
    font-family: "Ubuntu", sans-serif;
    color: var(--ink);
    position: relative;
  }

  /* Letterhead */
  .letterhead {
    position: absolute;
    left: 208px; top: 118px;
    width: 382px; height: 518px;
    background: linear-gradient(100deg, #ffffff 40%, #eceef1 100%);
    overflow: hidden;
  }
  .letterhead .edge-art { position: absolute; inset: 0; width: 100%; height: 100%; }
  .letterhead .brand {
    position: absolute; left: 26px; top: 20px;
    color: var(--brand-blue);
    font-weight: 700;
    line-height: 1;
  }
  .letterhead .brand-mark { font-size: 32px; letter-spacing: 1px; display: block; }
  .letterhead .brand-name { font-size: 7.5px; letter-spacing: 1.6px; display: block; margin-top: 3px; }

  .watermark {
    position: absolute; left: 96px; top: 248px;
    color: var(--watermark);
    font-weight: 700;
    line-height: 1;
  }
  .watermark-mark { display: block; font-size: 74px; letter-spacing: 4px; }
  .watermark-name { display: block; font-size: 16px; letter-spacing: 3px; margin-top: 6px; }

  .letter {
    position: absolute; left: 26px; top: 110px;
    width: 330px;
    font-size: 6.4px;
    line-height: 8.2px;
  }
  .letter p { margin-bottom: 8px; }
  .letter .gap { margin-bottom: 26px; }
  .letter .closing { margin-bottom: 10px; }

  .letter-footer {
    position: absolute; left: 20px; top: 486px;
    font-size: 6.2px; line-height: 10px;
  }
  .letter-footer strong { font-weight: 700; margin-right: 8px; }
  .letter-footer span { margin-right: 6px; }

  /* Folder */
  .folder {
    position: absolute;
    left: 629px; top: 90px;
    width: 430px; height: 553px;
    background: linear-gradient(160deg, #e4e5e7 0%, var(--folder-grey) 70%);
    overflow: hidden;
  }
  .folder .edge-art { position: absolute; inset: 0; width: 100%; height: 100%; }
  .folder .brand {
    position: absolute; left: 0; right: 0; top: 205px;
    text-align: center;
    color: var(--brand-blue);
    font-weight: 700;
    line-height: 1;
  }
  .folder .brand-mark { display: block; font-size: 104px; letter-spacing: 6px; }
  .folder .brand-name { display: block; font-size: 17px; letter-spacing: 3.4px; margin-top: 8px; }
</style>
</head>
<body>

<section class="letterhead" aria-label="Letterhead">
  <svg class="edge-art" viewBox="0 0 382 518" aria-hidden="true">
    <defs>
      <linearGradient id="lh-lower" x1="0" y1="0" x2="0" y2="1">
        <stop offset="0" stop-color="#3f82c4" stop-opacity="0"/>
        <stop offset="0.4" stop-color="#3a78bb"/>
        <stop offset="1" stop-color="#5a93cf"/>
      </linearGradient>
    </defs>
    <path d="M329 0 L346 0 Q392 250 318 518 L306 518 Q378 250 329 0Z" fill="var(--band-sky)"/>
    <path d="M346 0 L382 0 L382 518 L318 518 Q392 250 346 0Z" fill="var(--band-purple)"/>
    <path d="M382 230 L382 518 L322 518 Q372 400 382 230Z" fill="url(#lh-lower)"/>
  </svg>

  <div class="brand">
    <span class="brand-mark">BWP</span>
    <span class="brand-name">BRIGHTWELL POWER</span>
  </div>

  <div class="watermark" aria-hidden="true">
    <span class="watermark-mark">BWP</span>
    <span class="watermark-name">BRIGHTWELL POWER</span>
  </div>

  <div class="letter">
    <p>2210, Maple Crest Road<br>Springfield, CA 90210.</p>
    <p>January 29th, 2011</p>
    <p>Mr. Halloway<br>President, Halloway Family Center<br>518 Harbor Lane<br>Riverton, NY 10450</p>
    <p>Dear Mr. Halloway:</p>
    <p class="gap">In the first paragraph, one needs to give a brief introduction of oneself. One should also give reference to the purpose of the letter in brief.<br>The second paragraph needs to give the details of the letter and its need. This paragraph is mostly longer than the others and plays the main role in the letter. Keep the sentences short and to the point. Avoid using complex words and sentences.</p>
    <p>The third and last paragraph is the conclusion of the letter and can be kept short.</p>
    <p>Sincerely,</p>
    <p class="closing">(this is where the signature of the writer will be placed)</p>
    <p>Dana Whitlock<br>Read more at Letterwise: http://www.letterwise.com/guides/business-letter-layout-sample.html</p>
  </div>

  <footer class="letter-footer">
    <div><strong>Brightwell Power Ltd.</strong> 4410-72 Ave NW Edmonton, AB, T6B 2K8 Canada</div>
    <div><span>T: 780-555-0142</span><span>F: 888-555-0178</span><span>Email: info@brightwellpower.ca</span></div>
  </footer>
</section>

<section class="folder" aria-label="Presentation folder cover">
  <svg class="edge-art" viewBox="0 0 430 553" aria-hidden="true">
    <defs>
      <linearGradient id="fd-band" x1="0" y1="0" x2="0" y2="1">
        <stop offset="0" stop-color="#2f6db0"/>
        <stop offset="0.55" stop-color="#34508f"/>
        <stop offset="1" stop-color="#3b3477"/>
      </linearGradient>
      <linearGradient id="fd-dark" x1="0" y1="0" x2="1" y2="0">
        <stop offset="0" stop-color="#2e2e31"/>
        <stop offset="1" stop-color="#48484c"/>
      </linearGradient>
    </defs>
    <path d="M296 0 L312 0 Q445 250 390 553 L380 553 Q428 250 296 0Z" fill="var(--band-sky)"/>
    <path d="M312 0 L430 0 L430 553 L390 553 Q445 250 312 0Z" fill="url(#fd-band)"/>
    <path d="M0 553 L0 522 Q210 500 396 448 Q392 470 388 490 Q200 520 60 553Z" fill="#b9babd"/>
    <path d="M0 553 L0 532 Q210 512 388 470 Q385 515 382 553Z" fill="url(#fd-dark)"/>
    <path d="M0 524 Q205 502 396 452" fill="none" stroke="#ffffff" stroke-width="2"/>
  </svg>

  <div class="brand">
    <span class="brand-mark">BWP</span>
    <span class="brand-name">BRIGHTWELL POWER</span>
  </div>
</section>

</body>
</html>
```